Kestrel Facilities Business Card Design

We would now like to design business cards with the new Kestrel Facilities logo

Target Market(s)

Professional

Industry/Entity Type

Professional services

Contact Information for Business Card

Employee name, title, phone number, email address, corporate office address and logo.

Font styles to use
Sans Serif

Colors
0054AA
0677BA
7BADD7
CADEEF
E8F1F8

Requirements
Must have
• My logo
Should not have
• any other pictures or images besides my logo

```html
<!DOCTYPE html>
<html lang="en">
<head>
<meta charset="UTF-8">
<title>Kestrel Facilities Business Card</title>
<link rel="stylesheet" href="https://fonts.googleapis.com/css2?family=Montserrat:wght@400;500;700&display=swap">
<style>
  :root {
    --brand-blue: #3577bd;
    --stripe-grey: #a3a1a2;
    --ink: #1c1c1c;
    --card: #ffffff;
    --backdrop: #8a8a8a;
  }
  * { margin: 0; padding: 0; box-sizing: border-box; }
  html, body {
    width: 1160px;
    height: 1200px;
    overflow: hidden;
    background: var(--backdrop);
    font-family: "Montserrat", sans-serif;
  }
  .card {
    position: absolute;
    left: 199px;
    width: 777px;
    height: 442px;
    background: var(--card);
    overflow: hidden;
  }
  .card--front { top: 104px; }
  .card--back { top: 633px; }

  .brand {
    position: absolute;
    display: flex;
    align-items: center;
    color: var(--brand-blue);
    font-weight: 700;
  }
  .brand__square {
    background: var(--brand-blue);
    flex: none;
  }
  .brand__name { line-height: 1.05; }

  .card--front .brand { left: 73px; top: 150px; gap: 16px; }
  .card--front .brand__square { width: 54px; height: 54px; }
  .card--front .brand__name { font-size: 38px; }

  .card--back .brand { left: 0; right: 0; top: 170px; justify-content: center; gap: 22px; }
  .card--back .brand__square { width: 70px; height: 70px; }
  .card--back .brand__name { font-size: 48px; }

  .divider {
    position: absolute;
    left: 401px;
    top: 97px;
    width: 2px;
    height: 244px;
    background: var(--brand-blue);
  }
  .contact {
    position: absolute;
    left: 449px;
    top: 90px;
    color: var(--ink);
  }
  .contact__name {
    font-size: 27px;
    font-weight: 700;
    color: var(--brand-blue);
    letter-spacing: 0.2px;
    line-height: 1.2;
  }
  .contact__title {
    font-size: 20px;
    font-weight: 400;
    line-height: 1.3;
  }
  .contact__address {
    margin-top: 22px;
    font-size: 20px;
    line-height: 29px;
  }
  .contact__list {
    list-style: none;
    margin-top: 25px;
    font-size: 20px;
    line-height: 29px;
  }
  .contact__list li { display: flex; align-items: center; gap: 8px; }
  .contact__list svg { width: 18px; height: 18px; flex: none; fill: var(--brand-blue); }

  .footer-band {
    position: absolute;
    left: 0;
    bottom: 0;
    width: 777px;
    height: 442px;
  }
</style>
</head>
<body>

<section class="card card--front">
  <div class="brand">
    <span class="brand__square"></span>
    <span class="brand__name">Kestrel<br>Facilities</span>
  </div>

  <div class="divider"></div>

  <div class="contact">
    <h1 class="contact__name">DANA HOLLOWAY</h1>
    <p class="contact__title">Co-Founder</p>
    <p class="contact__address">4180 N. Harbor Lane<br>Suite 720 Westfield.14</p>
    <ul class="contact__list">
      <li>
        <svg viewBox="0 0 20 20" aria-hidden="true"><path d="M2 7c0-3 4-4 8-4s8 1 8 4v2h-4V7H6v2H2z"/><rect x="4" y="9" width="12" height="8" rx="1"/></svg>
        +254-160-47215
      </li>
      <li>
        <svg viewBox="0 0 20 20" aria-hidden="true"><path d="M1 4h18v12H1z M2 5l8 6 8-6" fill="var(--brand-blue)"/><path d="M2 5l8 6 8-6" fill="none" stroke="#fff" stroke-width="1.5"/></svg>
        info@kestrelfacilities.com
      </li>
      <li>
        <svg viewBox="0 0 20 20" aria-hidden="true"><circle cx="10" cy="10" r="9"/><path d="M5 6c2 0 3 1 3 3s-2 2-2 4M12 3c0 2 2 2 3 3M13 12c1 1 1 3 0 4" fill="none" stroke="#fff" stroke-width="1.5"/></svg>
        www.kestrelfacilities.com
      </li>
    </ul>
  </div>

  <svg class="footer-band" viewBox="0 0 777 442" aria-hidden="true">
    <polygon points="0,390 520,394 508,407 0,403" fill="var(--stripe-grey)"/>
    <polygon points="0,411 510,414 554,387 777,388 777,442 0,442" fill="var(--brand-blue)"/>
  </svg>
</section>

<section class="card card--back">
  <div class="brand">
    <span class="brand__square"></span>
    <span class="brand__name">Kestrel<br>Facilities</span>
  </div>
</section>

</body>
</html>
```